Web Design Concept for new social network

We need a fresh, vibrant, clean web design layout for a new social network that we are trying to put together.
The site itself will be stuffed with little jquery/css tricks to enable a better/better looking UI (this is where you come in).
Imagine you were re-imagining Rallyhub.. How would you have designed it? The new site, will have a lot of similar functions to RH, and then a few more.
I will need a great looking sign in page in addition to;
The main page will need to have the following elements;
- Profile header.
Profile picture and tabbed area for various pieces of meta data contact details, preferences etc
- A Post Wall (like the wall on RH, but its crossed with a chirply-esque global search/post). People can respond to not only the original message, but can reply to each individual reply.
Instead of LIKE, there will need to be a positive/negative/neutral style option (feel free to get creative with naming). The background of each post will reflect the average rating (pos/nuetral/neg) of the post itself.. so if 100 people click pos, 50 neutral and 1 negative, the bg will mainly be the positive colour).
The feed will include messages by default from many sources (rallyhub/chirply/work loop) there should be somewhere that these can be switched on and off...
Somewhere to post a message - again by default it will post to all networks, but should be able to switch off.
Images/Videos/Text can all be posted to the wall (if you can think of a better name than wall - please use that!)
- Notifications; rather than having them in a drop down menu like rh, i want them to be in a hidden div (one div for each type) that slides open to reveal the notifications.. The default will be that the divs are closed so if there is a new notification there will be a need for something to appear on the screen that the user can click. We will need 3 notification types.
- Calendar; collapsable
- Options for today/this week/month views etc
- Menu system to navigate to other screens.
This should be able to show available things like groups/pages/events (again feel free to rename).
The screens themselves should appear to be stacked (like stacked tiles).
- Search; there should be a search bar somewhere with various options being available.
- Modal popup. I will be using modal popups across the site so will want a consistant feel (should be able to display photos/videos etc)
I will upload some files over the next few days to support the above, but am really looking for your creativity here.
Sites I really like the style of:
- the NEW yardnook (check it out.. its awesome).
- quince
- chirply
I want a really clean interface, modern.. splashes of colour are fine (but only where it will enhance).
Updates
I have added a file to the uploads that gives an idea of how the notifications should be revealed.. Please do not read too much into any styling... i created the pdf just to show how i expect the notifications to be revealed, and that I expect there to be multiple notification types.
Although I deliberately didnt request adverts to be shown in the brief, i also didnt explicitly state that they shouldnt be! The site will NOT feature adverts so please do not show them on the design. Id much rather that the space be used to improve layout.
Target Market(s)
18 to 40 - again, think rallyhub/chirply/workloop
Industry/Entity Type
Events
Look and feel

```html
<!DOCTYPE html>
<html lang="en">
<head>
<meta charset="utf-8">
<title>HushLine – Profile</title>
<link href="https://fonts.googleapis.com/css2?family=Arimo:wght@400;700&family=Ubuntu:wght@400;500;700&display=swap" rel="stylesheet">
<style>
:root{
  --bg:#ebe9e7;
  --panel:#fbfbfb;
  --panel-soft:#f0efee;
  --dark:#4a4a4a;
  --darker:#2d2d2d;
  --text:#444;
  --muted:#777;
  --accent:#e9585a;
  --accent-soft:#f7787a;
  --line:#d6d6d6;
}
*{margin:0;padding:0;box-sizing:border-box}
html,body{width:1200px;height:874px;overflow:hidden}
body{background:radial-gradient(ellipse at 50% 40%,#f6f5f4 0%,var(--bg) 75%);font-family:Arimo,Arial,sans-serif;color:var(--text);position:relative;font-size:10px}
.abs{position:absolute}
a{color:var(--accent);text-decoration:none}

.topnav{left:677px;top:0;width:361px;height:32px;background:#5a5a5a;border-radius:0 0 4px 4px;display:flex;font-family:Ubuntu,sans-serif;font-size:14px}
.topnav span{color:#eee;padding:0 7px;line-height:30px;border-right:1px solid #6c6c6c}
.topnav span:last-child{border:none}
.brand{font-family:Ubuntu,sans-serif;font-weight:700;font-size:21px;color:#6a6a6a;display:flex;align-items:center;gap:6px}
.brand i{width:9px;height:9px;background:var(--accent);display:block}
.search{left:375px;top:40px;width:202px;height:31px;background:#fff;border:1px solid #ccc;font-family:Ubuntu,sans-serif;font-size:14px;color:#666;padding:7px 9px}
.search svg{position:absolute;right:10px;top:10px}
.sitenav{top:54px;font-family:Ubuntu,sans-serif;font-size:15px;color:#666;line-height:28px}
.sitenav.active{background:var(--accent);color:#fff;border-radius:3px;padding:0 11px}

.sidebar{left:176px;top:106px;width:101px;height:236px;background:var(--dark);border:1px solid #333;border-radius:4px;overflow:hidden}
.photo{background:linear-gradient(160deg,#6b4a3a,#b07a5a 50%,#2d2a3a);border-radius:6px}
.sidebar .photo{position:absolute;left:9px;top:8px;width:82px;height:85px}
.sidebar .name{position:absolute;left:11px;top:104px;color:#fff;font-weight:700;font-size:11px}
.sidemenu{position:absolute;top:130px;left:0;width:100%;list-style:none}
.sidemenu li{height:20px;line-height:20px;padding-left:11px;color:#ddd;font-weight:700;font-size:10px;border-top:1px solid #5c5c5c;border-bottom:1px solid #383838}
.sidemenu li.on{background:#111;color:#fff;height:22px;line-height:22px;margin-bottom:2px}
.friend{width:41px;height:42px;border:3px solid #fff;box-shadow:0 0 2px #aaa;background:linear-gradient(160deg,#caa58a,#7a5a48)}
.friendcount{left:178px;top:513px;width:98px;font-weight:700;font-size:10px;color:#555;border-top:1px solid #ddd;padding-top:6px}
.friendcount a{float:right;font-weight:400;font-size:9px;text-decoration:underline}

.card{background:var(--panel);border-radius:4px;box-shadow:0 0 3px rgba(0,0,0,.05)}
.profile{left:284px;top:105px;width:753px;height:144px}
.profile .photo{position:absolute;left:15px;top:18px;width:81px;height:85px;border:1px solid #222}
.edit{position:absolute;left:25px;top:111px;width:68px;height:19px;background:var(--accent);color:#fff;border-radius:3px;text-align:center;font-family:Ubuntu,sans-serif;font-size:15px;line-height:19px}
.profile h1{position:absolute;left:107px;top:17px;font-family:Ubuntu,sans-serif;font-weight:700;font-size:23px;color:#666}
.meta{position:absolute;left:107px;top:46px;font-size:11px;line-height:16px;color:#666}
.meta b{color:#444}
.divider{position:absolute;left:288px;top:14px;width:2px;height:118px;background:linear-gradient(#fff,#ddd,#fff)}
.facts{position:absolute;left:316px;top:22px;list-style:none;font-size:9.5px;line-height:15px;color:#555}
.facts li::before{content:"";display:inline-block;width:6px;height:6px;background:#d33;margin:0 7px 1px -15px}
.facts li{padding-left:15px}
.facts li.plain::before{visibility:hidden}

.wall{left:284px;top:263px;width:750px;height:494px}
.composer{position:absolute;left:10px;top:9px;width:730px;height:90px;background:var(--panel-soft)}
.composer .input{position:absolute;left:9px;top:9px;width:712px;height:34px;background:#fff;border:1px solid #ccc;padding:10px 11px;font-size:11px;color:#555}
.attach{position:absolute;left:10px;top:61px;font-size:11px;color:#555;display:flex;align-items:center;gap:12px}
.share{position:absolute;left:660px;top:58px;width:60px;height:19px;background:var(--accent);color:#fff;border-radius:3px;text-align:center;font-family:Ubuntu,sans-serif;font-size:15px;line-height:19px}
.lock{position:absolute;left:634px;top:62px}

.post-avatar{left:297px;top:380px;width:44px;height:44px;border-radius:6px;background:linear-gradient(160deg,#5a3a2a,#b58062)}
.post-user{left:351px;top:381px;color:var(--accent);font-weight:700;font-size:11px}
.post-img{left:349px;top:400px;width:95px;height:72px;border:3px solid #fff;box-shadow:0 0 2px #999;background:linear-gradient(#8ab0d8 0%,#9ab 40%,#b33 70%,#555 100%)}
.caption{left:451px;top:399px;font-size:11px;line-height:15px}
.caption .c1{color:var(--accent)}
.caption .c2{color:#444}
.actions{font-size:9.5px;color:var(--accent)}
.actions span{color:#bbb;margin:0 5px}
.time{left:349px;top:480px;font-size:11px;color:#555;display:flex;gap:5px;align-items:center}

.row{left:349px;width:634px}
.likebar{top:506px;height:21px;background:var(--accent-soft);font-size:9.5px;color:#222;padding:5px 0 0 22px}
.likebar::before{content:"";position:absolute;left:43px;top:-7px;border:7px solid transparent;border-top:0;border-bottom-color:var(--accent-soft)}
.likebar a{color:#fff}
.showall{top:532px;height:21px;background:#e6e6e6;border-bottom:1px solid #ccc;font-size:9.5px;font-style:italic;padding:5px 0 0 22px;color:var(--accent)}
.comment{height:36px;background:#e8e8e8;border-bottom:2px solid #d5d5d5;font-size:9.5px;color:#222}
.comment .av{position:absolute;left:5px;top:4px;width:29px;height:29px;border-radius:5px;background:linear-gradient(160deg,#e0c0a0,#b08060)}
.comment .who{position:absolute;left:41px;top:7px}
.comment .who a{color:var(--accent)}
.comment .ago{position:absolute;left:41px;top:22px;color:#555;display:flex;gap:4px;align-items:center}
.reply{top:637px;height:31px;background:#fff;border:1px solid #ccc;font-family:Ubuntu,sans-serif;font-size:14px;color:#555;padding:6px 10px}
.loader{top:673px;height:66px;background:linear-gradient(#fafafa,#e9e9e9);border:1px solid #ccc;border-radius:3px}
.loader svg{position:absolute;left:303px;top:20px}

.footer-line{left:164px;top:779px;width:874px;border-top:1px dotted #bbb}
.footer-links{left:166px;top:799px;font-size:10.5px;color:#888}
.footer-links a{color:var(--accent)}
</style>
</head>
<body>

<nav class="abs topnav"><span>Updates</span><span>My Profile</span><span>Messages</span><span>Settings</span><span>Sign Out</span></nav>

<div class="abs brand" style="left:175px;top:42px"><i></i>HushLine</div>

<div class="abs search">Enter Keyword
  <svg width="11" height="11" viewBox="0 0 11 11"><circle cx="4.5" cy="4.5" r="3.3" fill="none" stroke="#555" stroke-width="1.5"/><line x1="7" y1="7" x2="10" y2="10" stroke="#555" stroke-width="2"/></svg>
</div>

<div class="abs sitenav active" style="left:840px">Groups</div>
<div class="abs sitenav" style="left:928px">Pages</div>
<div class="abs sitenav" style="left:987px">Events</div>

<aside class="abs sidebar">
  <div class="photo" role="img" aria-label="Profile photo of Marcus Stanton"></div>
  <div class="name">Marcus Stanton</div>
  <ul class="sidemenu">
    <li class="on">Wall</li><li>Photos</li><li>Videos</li><li>Pages</li><li>Groups</li>
  </ul>
</aside>

<div class="abs friend" style="left:179px;top:349px" role="img" aria-label="Friend photo"></div>
<div class="abs friend" style="left:232px;top:349px" role="img" aria-label="Friend photo"></div>
<div class="abs friend" style="left:179px;top:402px" role="img" aria-label="Friend photo"></div>
<div class="abs friend" style="left:232px;top:402px" role="img" aria-label="Friend photo"></div>
<div class="abs friend" style="left:179px;top:454px" role="img" aria-label="Friend photo"></div>
<div class="abs friend" style="left:232px;top:454px" role="img" aria-label="Friend photo"></div>
<div class="abs friendcount">119 Friends <a>View All</a></div>

<section class="abs card profile">
  <div class="photo" role="img" aria-label="Profile photo of Marcus Stanton"></div>
  <div class="edit">Edit</div>
  <h1>Marcus Stanton</h1>
  <div class="meta"><b>Birth :</b> April 22, 1980<br><b>Country :</b> UK</div>
  <div class="divider"></div>
  <ul class="facts">
    <li>I'm Currently Live Portland, OR</li>
    <li>I'm in the Lakeside Ward</li>
    <li>I'm Single</li>
    <li>I Graduated from Ridgeview U</li>
    <li>I served my Mission in Bogota, Colombia</li>
    <li>My Super power would be able to fly!</li>
    <li class="plain">I love business, Being Creative, Basketball, Coaching Basketball, Comedy and lots of Laughing...</li>
  </ul>
</section>

<section class="abs card wall">
  <div class="composer">
    <div class="input">Dazzle the world... or just share something...</div>
    <div class="attach">Attach:
      <svg width="16" height="14"><rect x="1" y="3" width="12" height="10" fill="#f3c94a" stroke="#567"/><rect x="3" y="1" width="12" height="10" fill="#9cd" stroke="#567"/></svg>
      <svg width="18" height="15"><rect x="0" y="3" width="18" height="12" fill="#2a5aa0"/><rect x="0" y="0" width="18" height="3" fill="#222"/></svg>
      <svg width="14" height="14"><rect x="3" y="0" width="11" height="11" fill="#fff" stroke="#567"/><rect x="0" y="4" width="8" height="10" fill="#ddd" stroke="#567"/></svg>
      <span style="margin-left:22px">Instant Invite:</span>
      <svg width="14" height="22"><path d="M5 2v11l-3-2v4l5 6h6V11l-5-2V2z" fill="#35a7e8"/></svg>
    </div>
    <svg class="lock" width="22" height="10"><rect x="0" y="4" width="8" height="6" fill="#555"/><path d="M1.5 4V2.5a2.5 2.5 0 0 1 5 0V4" fill="none" stroke="#555" stroke-width="1.4"/><path d="M12 3h8l-4 4z" fill="#4a7fd0"/></svg>
    <div class="share">Share</div>
  </div>
</section>

<div class="abs post-avatar" role="img" aria-label="Poster avatar"></div>
<div class="abs post-user">User Name Here</div>
<div class="abs post-img" role="img" aria-label="Group photo of friends outdoors"></div>
<div class="abs caption">
  <div class="c1">Image Caption Here</div>
  <div class="c2">yeah i got you back :PPPPPP</div>
  <div class="actions" style="margin-top:3px">Like<span>|</span>Comment</div>
  <div class="actions" style="margin-top:13px">Positive<span>|</span>Negative<span>|</span>Neutral</div>
</div>
<div class="abs time"><svg width="14" height="12"><rect x="0" y="2" width="12" height="10" fill="#f3c94a" stroke="#567"/><rect x="2" y="0" width="12" height="9" fill="#9cd" stroke="#567"/></svg>16 hours ago</div>

<div class="abs row likebar"><svg style="position:absolute;left:6px;top:4px" width="13" height="12"><path d="M1 5h3v7H1zM5 5l3-5c2 0 2 2 1 4h4v3l-2 5H5z" fill="#ffd27a" stroke="#a66" stroke-width=".6"/></svg><a>Lena Sorell</a> and <a>Ana-Mae Sutton</a> like this</div>
<div class="abs row showall"><svg style="position:absolute;left:5px;top:4px" width="14" height="12"><path d="M1 1h12v8H6l-3 3V9H1z" fill="#fff" stroke="#888"/></svg>Show all 12 comments</div>

<div class="abs row comment" style="top:558px"><div class="av" role="img" aria-label="Commenter avatar"></div><div class="who"><a>Ana-Mae Sutton</a> like this</div><div class="ago"><svg width="14" height="12"><rect x="0" y="2" width="12" height="10" fill="#f3c94a" stroke="#567"/><rect x="2" y="0" width="12" height="9" fill="#9cd" stroke="#567"/></svg>about an hour ago</div></div>
<div class="abs row comment" style="top:597px"><div class="av" role="img" aria-label="Commenter avatar"></div><div class="who"><a>Ana-Mae Sutton</a> like this</div><div class="ago"><svg width="14" height="12"><rect x="0" y="2" width="12" height="10" fill="#f3c94a" stroke="#567"/><rect x="2" y="0" width="12" height="9" fill="#9cd" stroke="#567"/></svg>about an hour ago</div></div>

<div class="abs row reply">Drop some of your wisdom on em</div>
<div class="abs row loader">
  <svg width="28" height="28" viewBox="0 0 28 28">
    <circle cx="14" cy="3" r="2.4" fill="#333"/><circle cx="21.8" cy="6.2" r="2.2" fill="#444"/><circle cx="25" cy="14" r="2" fill="#666"/><circle cx="21.8" cy="21.8" r="1.9" fill="#777"/>
    <circle cx="14" cy="25" r="1.8" fill="#888"/><circle cx="6.2" cy="21.8" r="1.7" fill="#999"/><circle cx="3" cy="14" r="1.6" fill="#aaa"/><circle cx="6.2" cy="6.2" r="2.6" fill="#222"/>
  </svg>
</div>

<div class="abs footer-line"></div>
<div class="abs footer-links"><a>About</a> - <a>Help</a> - <a>Blog</a> - <a>Status</a> - <a>Jobs</a> - <a>Terms</a> - <a>Privacy</a> - <a>Advertisers</a> - <a>Businesses</a> - <a>Media</a> - <a>Developers</a> - <a>Resources</a> - <a>Directory</a></div>
<div class="abs brand" style="left:857px;top:790px"><i></i>HushLine</div>

</body>
</html>
```